New business card/stationary for a consulting company

I am looking for a clean and very professional looking business card for my consulting company as well as corresponding stationary. I am uploading our logo. I like simple and powerful for the feel. No graphics but I am open on everything else. Below is my contact information but would like the final to be in a version I can add my employees information into and print. Thank you.

Daniel Whitcombe
dan@ferncliffadvisory.com
2870 North 9th Avenue, Summit Floor, Elm Ridge, Illinois 60531
www.ferncliffadvisory.com

Industry/Entity Type

Consulting

Contact Information for Business Card

Daniel Whitcombe
dan@ferncliffadvisory.com
www.ferncliffadvisory.com

Font styles to use
Serif
Sans Serif

Requirements
Must have
• Our logo and the business card details.
Nice to have
• our website www.ferncliffadvisory.com

```html
<!DOCTYPE html>
<html lang="en">
<head>
<meta charset="UTF-8">
<title>Ferncliff Advisory — Business Card</title>
<link rel="stylesheet" href="https://fonts.googleapis.com/css2?family=Tenor+Sans&family=Lato:wght@400&display=swap">
<style>
  :root {
    --navy: #020066;
    --white: #ffffff;
    --page: #e9e8e6;
    --disc-light: #f4f3f2;
    --disc-mid: #dedcda;
    --disc-edge: #c9c7c5;
  }
  * { margin: 0; padding: 0; box-sizing: border-box; }
  html, body {
    width: 1200px;
    height: 900px;
    overflow: hidden;
    background: var(--page);
  }
  .business-card {
    position: absolute;
    left: 150px;
    top: 171px;
    width: 900px;
    height: 558px;
    background: var(--navy);
    color: var(--white);
    box-shadow: 0 10px 30px rgba(0,0,0,0.18);
  }
  .holder-name {
    position: absolute;
    left: 51px;
    top: 72px;
    font-family: "Tenor Sans", sans-serif;
    font-size: 26px;
    letter-spacing: 1.5px;
    text-transform: uppercase;
  }
  .address {
    position: absolute;
    left: 51px;
    top: 312px;
    font-family: "Lato", sans-serif;
    font-size: 22px;
    line-height: 34px;
  }
  .contact-list {
    position: absolute;
    left: 51px;
    top: 432px;
    list-style: none;
    font-family: "Lato", sans-serif;
    font-size: 22px;
    line-height: 33px;
  }
  .contact-list li {
    display: flex;
    align-items: center;
    gap: 9px;
  }
  .contact-icon { width: 19px; height: 19px; flex: none; }
  .brand-disc {
    position: absolute;
    left: 379px;
    top: 33px;
    width: 492px;
    height: 492px;
    border-radius: 50%;
    background: radial-gradient(circle at 40% 35%, var(--disc-light) 0%, var(--disc-mid) 65%, var(--disc-edge) 100%);
    display: flex;
    flex-direction: column;
    align-items: center;
    justify-content: center;
    gap: 22px;
  }
  .brand-mark {
    width: 46px;
    height: 46px;
    background: var(--navy);
  }
  .brand-name {
    font-family: "Tenor Sans", sans-serif;
    font-size: 31px;
    letter-spacing: 1.5px;
    color: var(--navy);
    text-transform: uppercase;
  }
</style>
</head>
<body>
  <article class="business-card">
    <h1 class="holder-name">Daniel Whitcombe</h1>
    <address class="address" style="font-style: normal;">
      2870 North 9th Avenue,<br>
      Summit Floor, Elm Ridge,<br>
      Illinois 60531
    </address>
    <ul class="contact-list">
      <li>
        <svg class="contact-icon" viewBox="0 0 20 20" aria-hidden="true">
          <rect x="1" y="4" width="18" height="12" fill="#ffffff"/>
          <path d="M1 4 L10 11 L19 4" fill="none" stroke="#020066" stroke-width="1.6"/>
        </svg>
        <span>dan@ferncliffadvisory.com</span>
      </li>
      <li>
        <svg class="contact-icon" viewBox="0 0 20 20" aria-hidden="true">
          <circle cx="10" cy="10" r="8.5" fill="#ffffff"/>
          <ellipse cx="10" cy="10" rx="3.5" ry="8.5" fill="none" stroke="#020066" stroke-width="1.3"/>
          <line x1="1.5" y1="10" x2="18.5" y2="10" stroke="#020066" stroke-width="1.3"/>
        </svg>
        <span>www.ferncliffadvisory.com</span>
      </li>
    </ul>
    <div class="brand-disc">
      <div class="brand-mark"></div>
      <p class="brand-name">Ferncliff Advisory</p>
    </div>
  </article>
</body>
</html>
```